Business Card and Letterhead Design Project

We need a business card template and letterhead designed for our new business.
Business Card
The information on the business card will be:
Logo
"slogan" - A whole new way to 401k
Person's Name
Title
Phone Number
Email Address
Website
We strive to make everything SIMPLE so please keep that in mind.
If you want to design something that would go on an odd shaped business card, that is fine, we are up for any ideas.
The Letterhead would have:
logo
business address
phone
fax
website
Here is a link to our logo files: http://qlnk.example/8rTw2Vp
we can provide the winning designer with higher quality files if needbe.

```html
<!DOCTYPE html>
<html lang="en">
<head>
<meta charset="utf-8">
<title>Verdell – Business Card</title>
<link rel="stylesheet" href="https://fonts.googleapis.com/css2?family=Open+Sans:wght@400;600;700&display=swap">
<style>
  :root {
    --page-bg: #ecebe8;
    --card-bg: #ffffff;
    --ink: #4a4a4a;
    --ink-soft: #3c3c3c;
    --brand-green: #7ab843;
    --tint-green: #f1f6ec;
    --rule: #8a8a8a;
    --on-green: #ffffff;
  }
  * { margin: 0; padding: 0; box-sizing: border-box; }
  html, body {
    width: 1200px; height: 1056px; overflow: hidden;
    background: var(--page-bg);
    font-family: "Open Sans", Arial, sans-serif;
  }
  .card {
    position: absolute;
    background: var(--card-bg);
    width: 500px; height: 838px;
    box-shadow: 0 2px 8px rgba(0,0,0,0.12);
    overflow: hidden;
  }
  .card--back { left: 90px; top: 109px; }
  .card--front { left: 620px; top: 109px; }

  .faint-mark {
    position: absolute;
    border-radius: 50%;
    background: var(--tint-green);
  }
  .card--back .faint-mark { width: 330px; height: 330px; left: 85px; top: 270px; }
  .card--front .faint-mark { width: 330px; height: 330px; left: 85px; top: 240px; }

  .wordmark {
    position: absolute;
    font-weight: 600;
    color: var(--ink);
    letter-spacing: -1px;
  }
  .card--back .wordmark {
    left: 0; right: 0; top: 360px;
    text-align: center; font-size: 86px; line-height: 1;
  }
  .back-url {
    position: absolute; left: 0; right: 0; bottom: 38px;
    text-align: center; font-size: 22px; letter-spacing: 4px;
    color: var(--ink-soft);
  }

  .brand-row {
    position: absolute; left: 42px; top: 58px;
    display: flex; align-items: center; height: 84px;
  }
  .brand-dot {
    width: 64px; height: 64px; border-radius: 50%;
    background: var(--brand-green);
  }
  .brand-divider {
    width: 2px; height: 84px; background: #cfcfcf; margin: 0 18px;
  }
  .card--front .wordmark { position: static; font-size: 70px; line-height: 1; }

  .slogan {
    position: absolute; left: 0; right: 0; top: 590px;
    text-align: center; font-size: 22px; letter-spacing: 2px;
    color: var(--ink-soft);
  }
  .slogan-rule {
    position: absolute; left: 0; right: 0; top: 626px;
    height: 2px; background: var(--rule);
  }
  .contact-band {
    position: absolute; left: 0; right: 0; top: 634px; bottom: 0;
    background: var(--brand-green);
    color: var(--on-green);
    padding: 18px 0 0 36px;
  }
  .person { font-size: 24px; font-weight: 700; margin-bottom: 18px; }
  .person .title { font-weight: 400; font-size: 21px; }
  .contact-line {
    display: flex; align-items: center;
    font-size: 21px; height: 40px;
  }
  .contact-line svg { width: 20px; height: 20px; margin-right: 12px; flex: none; }
</style>
</head>
<body>
  <section class="card card--back" aria-label="Business card back">
    <div class="faint-mark" aria-hidden="true"></div>
    <div class="wordmark">Verdell</div>
    <div class="back-url">www.verdell.example</div>
  </section>

  <section class="card card--front" aria-label="Business card front">
    <div class="faint-mark" aria-hidden="true"></div>
    <div class="brand-row">
      <div class="brand-dot" aria-hidden="true"></div>
      <div class="brand-divider" aria-hidden="true"></div>
      <div class="wordmark">Verdell</div>
    </div>
    <div class="slogan">A whole new way to 401k</div>
    <div class="slogan-rule"></div>
    <div class="contact-band">
      <div class="person">Person's Name, <span class="title">Title</span></div>
      <div class="contact-line">
        <svg viewBox="0 0 20 20" aria-hidden="true"><circle cx="10" cy="10" r="9" fill="none" stroke="#fff" stroke-width="1.6"/><path d="M7 5.5l2 2-1.2 1.4c.6 1.3 1.5 2.2 2.8 2.8L12 10.5l2 2-1.5 1.8C9 14 6 11 5.7 7z" fill="#fff"/></svg>
        123-456-7890
      </div>
      <div class="contact-line">
        <svg viewBox="0 0 20 20" aria-hidden="true"><rect x="2" y="5" width="16" height="11" rx="1" fill="#fff"/><path d="M2.5 5.5L10 11l7.5-5.5" fill="none" stroke="#7ab843" stroke-width="1.6"/></svg>
        info@verdell.example
      </div>
      <div class="contact-line">
        <svg viewBox="0 0 20 20" aria-hidden="true"><circle cx="10" cy="10" r="8.5" fill="#fff"/><g fill="none" stroke="#7ab843" stroke-width="1.2"><ellipse cx="10" cy="10" rx="3.5" ry="8.5"/><path d="M1.5 10h17M3 6h14M3 14h14"/></g></svg>
        www.verdell.example
      </div>
    </div>
  </section>
</body>
</html>
```